Tall fern bicycle rental

would like to have a bicycle rental website that has the ability to have a calender and be able to sign a liability waiver and pay all on line, We rent fat tire vorn bicycles

```html
<!DOCTYPE html>
<html lang="en">
<head>
<meta charset="utf-8">
<title>Tall Fern Bicycle Rental</title>
<link rel="stylesheet" href="https://fonts.googleapis.com/css2?family=Saira+Semi+Condensed:wght@500;600;700&family=Cabin:wght@400;500;600&display=swap">
<style>
:root{
  --blue:#1a74c4;
  --blue-bright:#2a93dc;
  --heading:#1563ad;
  --navy:#0f4d8c;
  --cell:#0e4c86;
  --footer:#103f76;
  --footer-bar:#0c3464;
  --text:#3e4a56;
  --muted:#8a96a2;
  --white:#ffffff;
}
*{margin:0;padding:0;box-sizing:border-box}
html,body{width:1200px;height:3881px;overflow:hidden}
body{position:relative;background:var(--white);font-family:"Cabin",sans-serif;color:var(--text)}
.abs{position:absolute}
.display{font-family:"Saira Semi Condensed",sans-serif;font-weight:700;color:var(--heading);line-height:1.1}
.btn{position:absolute;display:flex;align-items:center;justify-content:center;border-radius:30px;font-family:"Saira Semi Condensed",sans-serif;font-weight:600;font-size:19px;letter-spacing:.3px}
.btn-solid{background:var(--blue);color:var(--white)}
.btn-white{background:var(--white);color:var(--blue);box-shadow:0 4px 14px rgba(0,0,0,.15)}
.btn-outline{border:2px solid var(--blue);color:var(--blue);background:var(--white)}
.body-copy{font-size:17px;line-height:1.6}

/* header */
.brand{left:84px;top:14px;display:flex;align-items:center;gap:12px;width:300px}
.brand-mark{width:72px;height:72px;border-radius:50%;background:var(--blue);flex:none}
.brand-name{font-family:"Saira Semi Condensed",sans-serif;font-weight:700;font-size:28px;line-height:1;color:var(--blue);white-space:nowrap}
.brand-name small{display:block;font-size:11px;letter-spacing:1.5px;margin-top:4px}
.main-nav{top:38px;font-family:"Saira Semi Condensed",sans-serif;font-weight:500;font-size:18px;color:#1d2630;white-space:nowrap}
.main-nav.active{color:var(--blue-bright)}

/* hero */
.hero-bg{left:0;top:0;width:1200px;height:760px;background:linear-gradient(180deg,#eef4f9 0%,#dfe9f3 40%,#f4f8fb 80%,#fff 100%)}
.hero-title{left:90px;top:285px;font-size:51px}
.hero-copy{left:92px;top:415px;width:420px;color:#5b6670}
.slider-dots{left:1134px;top:320px;display:flex;flex-direction:column;gap:10px}
.slider-dots span{width:13px;height:13px;border-radius:50%;background:var(--white)}
.slider-dots span.current{background:transparent;border:2px solid var(--white)}

/* about */
.about-art{left:143px;top:790px;width:398px;height:398px;border-radius:50%;background:linear-gradient(180deg,#0e3f8c 0%,#1a66b8 55%,#2a8fd0 70%,#10509a 100%)}
.eyebrow{left:607px;top:822px;font-size:31px;color:var(--blue-bright)}
.about-title{left:607px;top:860px;font-size:46px;white-space:nowrap}
.about-copy{left:607px;top:932px;width:490px;color:#3a4652}
.about-copy p{margin-bottom:12px}

/* booking */
.book-title{left:151px;top:1386px;font-size:39px;color:var(--white);white-space:nowrap}
.book-copy{left:155px;top:1450px;width:430px;color:#e6f0fa;font-size:16px;line-height:1.5}
.book-copy p{margin-bottom:12px}
.calendar{left:623px;top:1334px;width:440px;box-shadow:0 8px 24px rgba(0,0,0,.25);background:var(--cell)}
.cal-head{height:53px;background:var(--white);display:flex;align-items:center;justify-content:center;gap:56px;font-family:"Saira Semi Condensed",sans-serif;font-weight:600;font-size:23px;color:var(--blue)}
.cal-head .arrow{color:#666;font-size:26px;font-weight:500}
.cal-days,.cal-grid{display:grid;grid-template-columns:repeat(7,1fr)}
.cal-days{height:38px;background:var(--blue-bright);align-items:center;text-align:center;color:var(--white);font-size:13px;font-weight:600}
.cal-grid div{height:52px;display:flex;align-items:center;justify-content:center;color:var(--white);font-size:21px;font-weight:600;border-right:1px solid rgba(255,255,255,.12);border-bottom:1px solid rgba(255,255,255,.12)}

/* how it works */
.how-bg{left:0;top:1764px;width:1200px;height:600px;background:linear-gradient(90deg,#fff 40%,#eef3f8 100%)}
.how-title{left:675px;top:1852px;font-size:34px}
.step{left:672px;display:flex;align-items:center;gap:14px}
.step-num{font-family:"Saira Semi Condensed",sans-serif;font-weight:500;font-size:64px;color:var(--blue-bright);width:30px;line-height:1}
.step-icon{width:76px;height:76px;border-radius:50%;border:2px solid var(--blue-bright);background:var(--white);display:flex;align-items:center;justify-content:center;margin-left:-16px;flex:none}
.step-title{font-family:"Saira Semi Condensed",sans-serif;font-weight:500;font-size:18px;color:#1d2630;white-space:nowrap}
.step-text{font-size:14px;color:var(--muted);margin-top:4px;white-space:nowrap}

/* testimonials */
.testimonials-title{left:0;top:2358px;width:1180px;text-align:center;font-size:37px}
.quote-photo{background:linear-gradient(180deg,#7d94ac 0%,#b8c6d3 50%,#5b6b78 100%)}
.quote-card{background:var(--white);box-shadow:0 4px 16px rgba(0,0,0,.12);text-align:center;font-size:14px;line-height:1.65;color:#555f69;padding:26px 22px 0}
.quote-card strong{display:block;margin-top:6px;color:#3a4450;font-weight:600}
.quote-card.featured{background:linear-gradient(180deg,#1158a4 0%,#2a93dc 100%);color:var(--white);font-size:16px;padding-top:34px}
.quote-card.featured strong{color:var(--white)}

/* journey */
.journey-bg{left:0;top:2850px;width:1200px;height:662px;background:linear-gradient(180deg,#fff 0%,#e8eef4 50%,#f2f5f8 100%)}
.journey-title{left:123px;top:3062px;font-size:39px;white-space:nowrap}
.journey-copy{left:124px;top:3166px;width:370px;color:#3a4652;line-height:1.5}

/* footer */
.footer{left:0;top:3512px;width:1200px;height:310px;background:var(--footer);color:var(--white)}
.footer-bar{left:0;top:3822px;width:1200px;height:59px;background:var(--footer-bar);color:#c9d7e6;font-size:12px;text-align:center;line-height:59px}
.footer-brand{left:150px;top:3580px;display:flex;flex-direction:column;align-items:center;gap:14px}
.footer-brand .brand-mark{width:120px;height:120px;background:var(--white)}
.footer-brand .brand-name{color:var(--white);font-size:22px}
.footer-col{top:3584px;color:#dbe6f2;font-size:15px}
.footer-col h3{font-family:"Saira Semi Condensed",sans-serif;font-weight:600;font-size:21px;color:var(--white);margin-bottom:14px;white-space:nowrap}
.footer-col li{list-style:none;line-height:27px;white-space:nowrap}
.socials{display:flex;gap:6px;margin-top:4px}
.socials span{width:30px;height:30px;border-radius:50%;border:2px solid var(--white)}
</style>
</head>
<body>

<!-- HERO -->
<div class="abs hero-bg" role="img" aria-label="Misty snowy mountain range"></div>
<svg class="abs" style="left:535px;top:60px" width="665" height="690" viewBox="0 0 665 690" role="img" aria-label="Rider jumping a fat tire bike over rocks">
  <defs><linearGradient id="heroPhoto" x1="0" y1="0" x2="0" y2="1">
    <stop offset="0" stop-color="#2a78c4"/><stop offset=".45" stop-color="#6ea6d6"/><stop offset=".7" stop-color="#9c9a94"/><stop offset="1" stop-color="#6d6a64"/></linearGradient></defs>
  <path d="M180 70 C250 20 330 60 420 40 C520 18 600 -10 665 0 L665 640 C610 660 540 610 470 650 C390 695 270 700 210 620 C150 540 30 540 8 410 C-12 290 80 150 180 70 Z" fill="url(#heroPhoto)"/>
</svg>

<div class="abs brand"><span class="brand-mark"></span><span class="brand-name">TALL FERN<small>BICYCLE RENTAL</small></span></div>
<nav>
  <span class="abs main-nav active" style="left:433px">HOME</span>
  <span class="abs main-nav" style="left:524px">ABOUT US</span>
  <span class="abs main-nav" style="left:645px">BIKE RENT</span>
  <span class="abs main-nav" style="left:770px">CALENDAR</span>
  <span class="abs main-nav" style="left:896px">BOOK NOW</span>
  <span class="abs main-nav" style="left:1026px">CONTACT</span>
</nav>

<h1 class="abs display hero-title">RENT BICYCLE FOR<br>YOUR JOURNEY</h1>
<p class="abs body-copy hero-copy">Lorem ipsum dolor sit amet consectetuer adipiscing elit Nam cursus Morbi ut mi Nullam enim</p>
<a class="btn btn-solid" style="left:86px;top:493px;width:188px;height:54px">BOOK NOW</a>
<div class="abs slider-dots"><span class="current"></span><span></span><span></span><span></span></div>

<!-- ABOUT -->
<div class="abs about-art" role="img" aria-label="Illustration of a cyclist under palm trees by a lake"></div>
<h2 class="abs display eyebrow">WELCOME</h2>
<h2 class="abs display about-title">ABOUT TALL FERN</h2>
<div class="abs body-copy about-copy">
  <p>Arna Sed porta Suspendisse quam leo molestie sed luctus quis feugiat in pede Fusce tellus Sed metus augue convall</p>
  <p>consequat nec porta vel lectus Nulla sit amet diam Duis non nunc Nulla rhoncus dictum metus Curabitur tristique mi condimentum orci Phasellus pellentesque aliquam</p>
</div>
<a class="btn btn-outline" style="left:600px;top:1105px;width:196px;height:62px">LEARN MORE</a>

<!-- BOOKING -->
<svg class="abs" style="left:0;top:1150px" width="1200" height="630" viewBox="0 0 1200 630" role="img" aria-label="Faded photo of a rider on a blue band">
  <defs><linearGradient id="bookBand" x1="0" y1="0" x2="1" y2="1">
    <stop offset="0" stop-color="#0d5aa8"/><stop offset=".6" stop-color="#1b72c2"/><stop offset="1" stop-color="#2a8fd6"/></linearGradient></defs>
  <path d="M0 0 C70 30 110 110 210 110 C330 110 430 100 540 104 C640 108 720 150 760 250 C800 360 760 520 660 585 C580 630 460 600 340 600 C220 600 90 620 0 615 Z" fill="url(#bookBand)"/>
</svg>
<h2 class="abs display book-title">BOOK BICYCLE NOW</h2>
<div class="abs book-copy">
  <p>Arna Sed porta Suspendisse quam leo molestie sed luctus quis feugiat in pede Fusce tellus Sed metus augue convall</p>
  <p>consequat nec porta vel lectus Nulla sit amet diam Duis non nunc Nulla rhoncus dictum metus Curabitur tris</p>
</div>
<a class="btn btn-white" style="left:154px;top:1587px;width:176px;height:51px">BOOK NOW</a>

<div class="abs calendar">
  <div class="cal-head"><span class="arrow">&lsaquo;</span><span>JUNE 2020</span><span class="arrow">&rsaquo;</span></div>
  <div class="cal-days"><span>MO</span><span>TU</span><span>WE</span><span>TH</span><span>FR</span><span>SA</span><span>SU</span></div>
  <div class="cal-grid">
    <div>1</div><div>2</div><div>3</div><div>4</div><div>5</div><div>6</div><div>7</div>
    <div>8</div><div>9</div><div>10</div><div>11</div><div>12</div><div>13</div><div>14</div>
    <div>15</div><div>16</div><div>17</div><div>18</div><div>19</div><div>20</div><div>21</div>
    <div>22</div><div>23</div><div>24</div><div>25</div><div>26</div><div>27</div><div>28</div>
    <div></div><div>30</div><div>31</div><div></div><div></div><div></div><div></div>
  </div>
</div>

<!-- HOW IT WORKS -->
<div class="abs how-bg"></div>
<svg class="abs" style="left:0;top:1764px" width="760" height="590" viewBox="0 0 760 590" role="img" aria-label="Two friends riding fat tire bikes by the coast">
  <defs><linearGradient id="howPhoto" x1="0" y1="0" x2="1" y2="1">
    <stop offset="0" stop-color="#a9b6c2"/><stop offset=".45" stop-color="#7f8c7a"/><stop offset=".8" stop-color="#55664a"/><stop offset="1" stop-color="#eef3f8"/></linearGradient></defs>
  <path d="M0 0 L640 0 C700 120 740 300 720 420 C700 520 620 570 520 560 C400 550 300 590 160 580 C90 575 40 560 0 555 Z" fill="url(#howPhoto)"/>
</svg>
<h2 class="abs display how-title">HOW IT WORKS</h2>

<div class="abs step" style="top:1920px">
  <span class="step-num">1</span>
  <span class="step-icon"><svg width="40" height="28" viewBox="0 0 40 28" fill="none" stroke="#2a93dc" stroke-width="2"><circle cx="9" cy="19" r="7"/><circle cx="31" cy="19" r="7"/><path d="M9 19 L16 7 L27 7 L31 19 M16 7 L21 19 L27 7 M14 4 H19"/></svg></span>
  <div><div class="step-title">CHOOSE YOUR BICYCLE</div><div class="step-text">Lorem ipsum dolor sit amet consectetuer adipisc</div></div>
</div>
<div class="abs step" style="top:2027px">
  <span class="step-num">2</span>
  <span class="step-icon"><svg width="34" height="34" viewBox="0 0 34 34" fill="none" stroke="#2a93dc" stroke-width="2"><rect x="3" y="6" width="28" height="25" rx="3"/><path d="M3 13 H31 M10 3 V9 M24 3 V9"/><path d="M9 19 h3 M16 19 h3 M23 19 h3 M9 25 h3 M16 25 h3"/></svg></span>
  <div><div class="step-title">SELECT YOUR DATE &amp; TIME</div><div class="step-text">Lorem ipsum dolor sit amet consectetuer adipi</div></div>
</div>
<div class="abs step" style="top:2133px">
  <span class="step-num">3</span>
  <span class="step-icon"><svg width="38" height="28" viewBox="0 0 38 28" fill="none" stroke="#2a93dc" stroke-width="2"><rect x="2" y="3" width="34" height="22" rx="3"/><path d="M2 10 H36 M7 17 H17"/><circle cx="28" cy="18" r="3"/></svg></span>
  <div><div class="step-title">PAY &amp; ENJOY YOUR JOURNEY</div><div class="step-text">Lorem ipsum dolor sit amet consectetuer</div></div>
</div>

<!-- TESTIMONIALS -->
<h2 class="abs display testimonials-title">WHAT PEOPLE SAYS</h2>

<div class="abs quote-photo" style="left:92px;top:2468px;width:303px;height:203px" role="img" aria-label="Cyclist riding along a beach"></div>
<div class="abs quote-card" style="left:110px;top:2631px;width:267px;height:176px">Lorem ipsum dolor sit amet consectetuer adipiscing elit Nam cursus Morbi ut mi Nullam enim leo egestas id condimentum<strong>By Author Name</strong></div>

<div class="abs quote-photo" style="left:430px;top:2444px;width:345px;height:233px;background:linear-gradient(180deg,#2c5c9a 0%,#7aa0c8 55%,#46505a 100%)" role="img" aria-label="Cyclist standing with a bike on a hilltop"></div>
<div class="abs quote-card featured" style="left:449px;top:2628px;width:305px;height:206px">Lorem ipsum dolor sit amet consectetuer adipiscing elit Nam cursus Morbi ut mi Nullam enim leo egestas id condimentum<strong>By Author Name</strong></div>

<div class="abs quote-photo" style="left:805px;top:2468px;width:303px;height:203px;background:linear-gradient(180deg,#5d7690 0%,#c7cfd4 45%,#4c4a44 100%)" role="img" aria-label="Cyclist on rocks by a lake at sunset"></div>
<div class="abs quote-card" style="left:823px;top:2631px;width:265px;height:176px">Lorem ipsum dolor sit amet consectetuer adipiscing elit Nam cursus Morbi ut mi Nullam enim leo egestas id condimentum<strong>By Author Name</strong></div>

<!-- JOURNEY -->
<div class="abs journey-bg" role="img" aria-label="Misty snowy mountain range"></div>
<svg class="abs" style="left:595px;top:2855px" width="605" height="600" viewBox="0 0 605 600" role="img" aria-label="Mountain biker in a helmet riding over rocks">
  <defs><linearGradient id="journeyPhoto" x1="0" y1="0" x2="0" y2="1">
    <stop offset="0" stop-color="#2f7dc8"/><stop offset=".5" stop-color="#7eaed8"/><stop offset=".8" stop-color="#8b8780"/><stop offset="1" stop-color="#5f5b56"/></linearGradient></defs>
  <path d="M200 90 C280 60 320 0 430 10 C520 18 560 60 605 50 L605 530 C540 520 470 600 370 598 C280 596 240 540 160 500 C60 450 -10 380 5 280 C20 170 120 120 200 90 Z" fill="url(#journeyPhoto)"/>
</svg>
<h2 class="abs display journey-title">START YOUR JOURNEY<br><span style="color:var(--navy)">WITH TALL FERN</span></h2>
<p class="abs body-copy journey-copy">Aonsequat nec porta vel lectus Nulla sit amet diam Duis non nunc Nulla rhoncus dictum metus Curabitur tristique mi condimentum orci Phasellus pellentesque aliquam</p>
<a class="btn btn-white" style="left:115px;top:3294px;width:184px;height:57px">BOOK NOW</a>

<!-- FOOTER -->
<footer class="abs footer"></footer>
<div class="abs footer-brand"><span class="brand-mark"></span><span class="brand-name">Tall Fern</span></div>
<div class="abs footer-col" style="left:359px"><h3>QUICK LINKS</h3><ul><li>Home</li><li>About</li><li>Rent bicycles</li><li>Testimonials</li></ul></div>
<div class="abs footer-col" style="left:538px"><h3>RESOURCES</h3><ul><li>Blogs</li><li>Book Now</li><li>Calendar</li><li>Contact Us</li></ul></div>
<div class="abs footer-col" style="left:702px"><h3>CONTACT US</h3><ul><li>42 Alder Row Suite 5</li><li>Pinecrest 20418 PC</li><li>555.014.2276</li><li>hello@tallfernrides.example</li></ul></div>
<div class="abs footer-col" style="left:918px"><h3>FOLLOW US</h3><div class="socials"><span></span><span></span><span></span><span></span></div></div>
<div class="abs footer-bar">&copy; 2020 Company Name&nbsp; All right reserved</div>

</body>
</html>
```